Corvane Lending Partners. Professional and Established Company

A full service finance company specializing in obtaining capital for small business. Business Lending advisor, helping small business owners access the capital they need to launch, grow, or sustain their business. Many of our programs offer flexible guidelines to overcome common obstacles such as credit score, credit history, and time in business, financials, and industry type. Our streamlined funding process makes getting a business loan, business line of credit, stated income commercial real estate loan, a smooth and stress free experience.SOME OF THE MOST COMMON NEEDS FOR BUSINESS CAPITAL:• Working Capital• Debt Consolidations (loans, merchant cash advances, etc.)• Payroll• Operating Expenses• Inventory• Equipment Financing• Commercial Real Estate (Purchase, Fix & Flip, Rehab, Renovations)• Business Acquisitions• Business ExpansionWe like the websites:www.quillmorecf.com they are in the same industry and provide the same servicesWe are wanting to be able to update when we do press releases and such using Word Press. Our look should be very professional and we will be adding Our Team Professional Bios and Headshots.

Industry/Entity Type

Finance

Number of Pages Required

5+ page

Font styles to use
Serif
Sans Serif

Requirements
Must have
• We want to copy quillmorecf.com
• We need:
• Home Page
• About Us
• Loan Programs
• Loan Criteria
• News
• Apply Now
• Contact
Nice to have
• See quillmorecf.com
Should not have
• Need professional design. Nothing bright or abstract

```html
<!DOCTYPE html>
<html lang="en">
<head>
<meta charset="utf-8">
<title>Corvane Lending Partners</title>
<link rel="stylesheet" href="https://fonts.googleapis.com/css2?family=Cinzel:wght@400;600&family=Lato:wght@400;700&display=swap">
<style>
:root{
  --navy:#1c3a72;
  --blue:#1f5cb3;
  --blue-deep:#1b4f9c;
  --ink:#222;
  --muted:#777;
  --light:#f4f4f5;
  --white:#fff;
  --stripe:#a9b3c1;
}
*{margin:0;padding:0;box-sizing:border-box}
html,body{width:1200px;height:3846px;overflow:hidden}
body{position:relative;background:var(--white);font-family:"Lato",Arial,sans-serif;color:var(--ink)}
.abs{position:absolute}
.serif{font-family:"Cinzel",Georgia,serif}

/* header */
.site-header{position:absolute;left:0;top:0;width:1200px;height:103px;background:var(--white);border-top:4px solid var(--blue)}
.brand{position:absolute;left:113px;top:22px;font-family:"Cinzel",Georgia,serif;font-weight:600;color:var(--navy);line-height:1}
.brand .name{font-size:30px;letter-spacing:2px;display:block}
.brand .sub{font-size:15px;letter-spacing:2.4px;display:block;margin-top:6px}
.contact-line{position:absolute;right:112px;top:18px;font-size:12px;color:#444;display:flex;align-items:center;gap:10px}
.contact-line .dot{width:10px;height:10px;border-radius:50%;background:var(--navy)}
.contact-line .sep{color:#aaa}
.main-nav{position:absolute;top:62px;left:0;width:1200px;font-size:14px;color:#333}
.main-nav span{position:absolute}

/* hero */
.hero{position:absolute;left:0;top:103px;width:1200px;height:710px}
.hero-photo{position:absolute;inset:0;background:linear-gradient(120deg,#6f5c48 0%,#a89682 30%,#cfc3b2 50%,#8a7a68 75%,#4b3f33 100%)}
.hero-shade{position:absolute;inset:0;background:rgba(30,24,18,.28)}
.hero-title{position:absolute;left:0;width:1200px;text-align:center;color:var(--white);font-family:"Cinzel",Georgia,serif}
.hero-title.t1{top:205px;font-size:76px;letter-spacing:6px;line-height:1}
.hero-title.t2{top:292px;font-size:46px;letter-spacing:5px;line-height:1}
.hero-copy{position:absolute;top:297px;left:0;width:1200px;text-align:center;color:var(--white);font-size:15px;line-height:33px;margin-top:0}
.hero-copy{top:300px}
.apply-btn{position:absolute;left:510px;top:395px;width:180px;height:52px;border-radius:26px;background:var(--blue);color:var(--white);font-size:15px;font-weight:700;text-align:center;line-height:52px;letter-spacing:.5px}
.loan-bar{position:absolute;left:0;top:571px;width:1200px;height:139px;background:rgba(15,15,18,.82)}
.loan{position:absolute;top:38px;width:200px;margin-left:-100px;text-align:center}
.loan .lt{color:var(--white);font-size:14px;font-weight:700;letter-spacing:.3px}
.loan .la{color:#5b8fd6;font-size:13px;margin-top:12px}
.loan-div{position:absolute;top:34px;width:1px;height:70px;background:rgba(255,255,255,.3)}

/* welcome */
.welcome{position:absolute;top:902px;left:0;width:1200px;text-align:center;font-family:"Cinzel",Georgia,serif;font-size:52px;color:var(--ink);letter-spacing:1px}
.welcome b{color:var(--blue);font-weight:600}

/* about */
.about{position:absolute;left:0;top:1018px;width:1200px;height:354px}
.about-photo{position:absolute;right:0;top:0;width:640px;height:354px;background:linear-gradient(135deg,#c9cdd2,#eceef0 45%,#7f9bc4 60%,#d8dbde)}
.about-stripe{position:absolute;left:0;top:0;width:760px;height:354px;background:var(--stripe);clip-path:polygon(0 0,716px 0,640px 100%,0 100%)}
.about-panel{position:absolute;left:0;top:0;width:720px;height:354px;background:var(--blue);clip-path:polygon(0 0,716px 0,576px 100%,0 100%)}
.about h2{position:absolute;left:113px;top:52px;color:var(--white);font-family:"Cinzel",Georgia,serif;font-weight:400;font-size:30px;letter-spacing:1px}
.about p{position:absolute;left:113px;top:113px;width:540px;color:var(--white);font-size:13.5px;line-height:33px}
.read-more{position:absolute;left:113px;top:276px;color:var(--white);font-size:13px;letter-spacing:.5px}

/* team */
.team{position:absolute;left:0;top:1372px;width:1200px;height:628px;background:var(--light)}
.section-title{position:absolute;left:0;width:1200px;text-align:center;font-family:"Cinzel",Georgia,serif;font-size:52px;color:var(--ink);letter-spacing:1px}
.section-title b{color:var(--blue);font-weight:400}
.member{position:absolute;top:203px;width:260px;margin-left:-130px;text-align:center}
.headshot{width:200px;height:200px;border-radius:50%;margin:0 auto;background:radial-gradient(circle at 50% 40%,#c8b3a0,#6f7f98)}
.member .nm{font-size:20px;margin-top:30px;color:var(--ink)}
.member .rl{font-size:11px;color:#555;margin-top:10px}
.socials{display:flex;justify-content:center;gap:6px;margin-top:16px}
.socials i{width:30px;height:30px;border-radius:50%;background:var(--navy)}
.socials i+i{background:#2d8fe0}

/* services */
.service{position:absolute;width:397px;text-align:center}
.service .img{width:100%;height:262px}
.service h3{font-size:22px;font-weight:700;color:var(--ink);margin-top:32px}
.service p{font-size:13px;color:var(--muted);line-height:25px;width:260px;margin:14px auto 0}

/* footer */
.footer-rule{position:absolute;left:113px;top:3598px;width:974px;height:1px;background:#e3e3e3}
.footer-brand{top:3650px}
.footer-nav{position:absolute;right:113px;top:3650px;font-size:13px;color:#333;letter-spacing:.4px}
.footer-nav .sl{color:#999;margin:0 8px}
.touch{position:absolute;left:936px;top:3693px;width:149px;height:44px;border-radius:22px;background:#c7c7c7;color:var(--white);font-size:12px;text-align:center;line-height:44px;letter-spacing:.5px}
.bottom-bar{position:absolute;left:0;top:3782px;width:1200px;height:64px;background:var(--blue-deep)}
.bottom-bar .icons{position:absolute;left:113px;top:16px;display:flex;gap:10px}
.bottom-bar .icons i{width:32px;height:32px;border-radius:50%;border:2px solid var(--white)}
.copy{position:absolute;right:113px;top:24px;color:var(--white);font-size:12px}
</style>
</head>
<body>

<header class="site-header">
  <div class="brand"><span class="name">CORVANE</span><span class="sub">LENDING PARTNERS</span></div>
  <div class="contact-line">
    <span>&#9742; Phone : 1 800 555 0142</span><span class="sep">|</span>
    <span>&#9993; info@companyname.com</span><span class="sep">|</span>
    <span class="dot"></span><span class="dot"></span><span class="dot"></span><span class="dot"></span>
  </div>
  <nav class="main-nav">
    <span style="left:420px">Home</span>
    <span style="left:493px">About Us</span>
    <span style="left:589px">Loan Programs</span>
    <span style="left:722px">Loan Criteria</span>
    <span style="left:843px">News</span>
    <span style="left:919px">Apply Now</span>
    <span style="left:1032px">Contact</span>
  </nav>
</header>

<section class="hero">
  <div class="hero-photo" role="img" aria-label="Warm office lobby interior with sofa, potted plants and framed mirror"></div>
  <div class="hero-shade"></div>
  <div class="hero-title t1" style="top:100px">CORVANE</div>
  <div class="hero-title t2" style="top:200px">LENDING PARTNERS</div>
  <p class="hero-copy">Sed ut perspiciatis unde omnis iste natus error sit voluptatem accusantium doloremque<br>laudantium, totam rem inventore veritatis et quasi architecto beatae</p>
  <div class="apply-btn">APPLY NOW</div>
  <div class="loan-bar">
    <svg class="abs" style="left:66px;top:58px" width="16" height="22" viewBox="0 0 16 22"><path d="M12 2 3 11l9 9" fill="none" stroke="#fff" stroke-width="3"/></svg>
    <svg class="abs" style="left:1116px;top:58px" width="16" height="22" viewBox="0 0 16 22"><path d="M4 2l9 9-9 9" fill="none" stroke="#fff" stroke-width="3"/></svg>
    <div class="loan" style="left:180px"><div class="lt">OFFICE LOANS</div><div class="la">$3,90,903</div></div>
    <div class="loan-div" style="left:290px"></div>
    <div class="loan" style="left:392px"><div class="lt">HOSPITALITY LOANS</div><div class="la">$3,90,000</div></div>
    <div class="loan-div" style="left:510px"></div>
    <div class="loan" style="left:626px"><div class="lt">MULTIFAMILY LOANS</div><div class="la">$5,46,909</div></div>
    <div class="loan-div" style="left:740px"></div>
    <div class="loan" style="left:826px"><div class="lt">LAND LOANS</div><div class="la">$12.5 Million</div></div>
    <div class="loan-div" style="left:926px"></div>
    <div class="loan" style="left:1020px"><div class="lt">RETAIL LOANS</div><div class="la">$16,900,000</div></div>
  </div>
</section>

<h1 class="welcome" style="font-weight:400">Welcome to <b>Corvane</b></h1>

<section class="about">
  <div class="about-photo" role="img" aria-label="Business team seen from above joining blue puzzle pieces on a table"></div>
  <div class="about-stripe"></div>
  <div class="about-panel"></div>
  <h2>About Us</h2>
  <p>Sed ut perspiciatis unde omnis iste natus error sit voluptatem accusantium doloremque laudantium, totam rem aperiam, eaque ipsa quae ab illo inventore veritatis et quasi architecto beatae vitae dicta sunt exo enim ipsam voluptatem quia voluptas sit aspernatur aut odit aut fugit, sed quia consequuntur magni dolores.</p>
  <div class="read-more">READ MORE &nbsp;&raquo;</div>
</section>

<section class="team">
  <h2 class="section-title" style="top:90px;font-weight:400">Our <b>Team</b></h2>
  <div class="member" style="left:213px"><div class="headshot" role="img" aria-label="Headshot of team member Prakvala"></div><div class="nm">Prakvala</div><div class="rl">Financial Advisor</div><div class="socials"><i></i><i></i></div></div>
  <div class="member" style="left:472px"><div class="headshot" role="img" aria-label="Headshot of team member Quis autem vel"></div><div class="nm">Quis autem vel</div><div class="rl">Financial Advisor</div><div class="socials"><i></i><i></i></div></div>
  <div class="member" style="left:731px"><div class="headshot" role="img" aria-label="Headshot of team member Suquis nostruh"></div><div class="nm">Suquis nostruh</div><div class="rl">Financial Advisor</div><div class="socials"><i></i><i></i></div></div>
  <div class="member" style="left:990px"><div class="headshot" role="img" aria-label="Headshot of team member Nemo enim ipsam"></div><div class="nm">Nemo enim ipsam</div><div class="rl">Financial Advisor</div><div class="socials"><i></i><i></i></div></div>
</section>

<h2 class="section-title" style="top:2102px;font-weight:400">What we <b>Provide</b></h2>

<div class="service" style="left:0;top:2228px"><div class="img" role="img" aria-label="Hands reviewing financial charts beside a laptop" style="background:linear-gradient(135deg,#5d7288,#c9d2dc)"></div><h3>Working Capital</h3><p>Sed ut perspiciatis unde omnis iste natus error sit voluptatem accusantium doloremque</p></div>
<div class="service" style="left:403px;top:2228px"><div class="img" role="img" aria-label="Older couple reviewing paperwork at a table" style="background:linear-gradient(135deg,#b39a7c,#efe6da)"></div><h3>Debt Consolidations</h3><p>Sed ut perspiciatis unde omnis iste natus error sit voluptatem accusantium doloremque</p></div>
<div class="service" style="left:803px;top:2228px"><div class="img" role="img" aria-label="Person using a phone at a desk" style="background:linear-gradient(135deg,#a68a78,#e9e2da)"></div><h3>Payroll</h3><p>Sed ut perspiciatis unde omnis iste natus error sit voluptatem accusantium doloremque</p></div>

<div class="service" style="left:0;top:2674px"><div class="img" role="img" aria-label="Team pointing at printed charts on a table" style="background:linear-gradient(135deg,#c7a58a,#8fa7bd)"></div><h3>Operating Expenses</h3><p>Sed ut perspiciatis unde omnis iste natus error sit voluptatem accusantium doloremque</p></div>
<div class="service" style="left:403px;top:2674px"><div class="img" role="img" aria-label="Hands holding a tablet showing a stock list" style="background:linear-gradient(135deg,#6f6a66,#b9c3cf)"></div><h3>Inventory</h3><p>Sed ut perspiciatis unde omnis iste natus error sit voluptatem accusantium doloremque</p></div>
<div class="service" style="left:803px;top:2674px"><div class="img" role="img" aria-label="Model house beside stacks of coins" style="background:linear-gradient(135deg,#8a7a6a,#e2d3c2)"></div><h3>Equipment Financing</h3><p>Sed ut perspiciatis unde omnis iste natus error sit voluptatem accusantium doloremque</p></div>

<div class="service" style="left:0;top:3120px"><div class="img" role="img" aria-label="Modern building with pool at dusk" style="background:linear-gradient(180deg,#3c5a86,#c38a4c)"></div><h3>Commercial Real Estate</h3><p>Sed ut perspiciatis unde omnis iste natus error sit voluptatem accusantium doloremque</p></div>
<div class="service" style="left:403px;top:3120px"><div class="img" role="img" aria-label="Business handshake in an office" style="background:linear-gradient(135deg,#8da0b5,#d7dfe8)"></div><h3>Business Acquisitions</h3><p>Sed ut perspiciatis unde omnis iste natus error sit voluptatem accusantium doloremque</p></div>
<div class="service" style="left:803px;top:3120px"><div class="img" role="img" aria-label="Hand placing puzzle pieces below a rising arrow" style="background:linear-gradient(135deg,#3a3a3c,#9a9a9c)"></div><h3>Business Expansion</h3><p>Sed ut perspiciatis unde omnis iste natus error sit voluptatem accusantium doloremque</p></div>

<div class="footer-rule"></div>
<div class="brand footer-brand"><span class="name">CORVANE</span><span class="sub">LENDING PARTNERS</span></div>
<nav class="footer-nav">HOME<span class="sl">/</span>ABOUT US<span class="sl">/</span>LOAN PROGRAMS<span class="sl">/</span>LOAN CRITERIA<span class="sl">/</span>NEWS<span class="sl">/</span>APPLY NOW<span class="sl">/</span>CONTACT</nav>
<div class="touch">GET IN TOUCH</div>

<footer class="bottom-bar">
  <div class="icons"><i></i><i></i><i></i><i></i><i></i></div>
  <div class="copy">&copy; Copyright 2018.Companyname.All Rights Reserved &nbsp;|&nbsp; Privacy Policy</div>
</footer>

</body>
</html>
```